Verpackungen für Shampoos
Zielgruppe
Wir sind ein kleines Familienunternehmen mit 2-3 Friseurfilialen und Onlineshop im Naturfriseurbereich, arbeiten mit ökologischen, nachhaltigen und natürlichen Produkten und vertreiben unsere eigene Haarbürste. Wir betreiben mit Sol Verde unsere eigene Marke in diesem Bereich. Erste Produkte, wie eine eigene Haarbürste sind bereits vorhanden und entstanden.
Für unsere erste Shampoo Serie suchen wir ein klares, cleanes und hochwertiges Design. Die 200ml Shampooflasche kommt komplett in weiß und besteh aus recyceltem Material. Es soll klar die ökologisch nachhaltige und etwas höherpreisige Marke kommuniziert werden. Dabei sehen wir vom Stil „weniger ist mehr“ als ganz klare Designvorgabe. Anbei auch ein Beispiel von Pavura, die das ganze sehr schön umgesetzt haben.
Die INCI sind noch nicht final. Es wäre schön, wenn hier ein Platzhalter eingefügt würde. Da eine der Hauptzielgruppen auch Österreicher sind, würden wir uns über ein kleines „Made in Austria“ auf der Vorderseite (evtl. ganz unten auf der Flasche) freuen.
Insgesamt sind es vier verschiedene Shampoos, die aus der gleichen Serie stammen. Es wäre schön, wenn man diese auch direkt unterscheiden könnte. Vielleicht durch ein grafisches Element, oder einfach nur durch die verschiedenen Namenserweiterungen. Hier die Aufstellung mit den Erweiterungen:
Es werden 4 verschiedene Shampoos, die Namen sind:
Change - Strapaziertes Haar
Care - Normales Haar
Sensitiv - Empfindliche Kopfhaut
Balancing - Fettiges Haar
Zielgruppe:
Weiblich, 30-60 Jahre, mittleres bis gehobenes Einkommen, nachhaltig, ökologisch, natürlich, legt Wert auf hochwertige Produkte und Dienstleistungen, achtet auf Konsum.
Aufgabenstellung
Die Landingpage zur Bürste ist hier erreichbar (Beispiel):
Vielleicht hilft das etwas um das Design und die Tonality aufzuschnappen: https://sol-verde.de/gold-birch-wildschweinborstenbuerste/
Es wäre super, wenn das Design der Flasche ähnlich klar und strukturiert ist.
Die Shampoos sind komplett vegan und made in Austria. Die beiden Aspekte sollten in Design auch aufgegriffen werden. Da wir einen 4 farbigen Tamponade/Siebdruck auf der Flasche anwenden, stehen leider nicht so viele Farben zur Verfügung (3-4).
Link zur Flasche:
https://www.brumoxa.com/de/kosmetik/varleno/varleno-tubica/flasche-heavy-200ml-24-410-plastik
Des Weiteren kann sich noch am Sol Verde Haarkonzept und unserem Dienstleistungsflyer orientiert werden.
Benefits:
-       Pflegt das Haar, hält es geschmeidig
- Bio Shampoo Konzentrat
-       Die Grundlage für gesunde Kopfhaut und schönes Haar*
-       Vermindert Spliss*
-       Hält die Haare natürlich geschmeidig
-       Regt die Durchblutung der Kopfhaut an
-       Verteilt Nährstoffe von der Wurzel bis in die Spitzen*
-       Verbessert das Kopfhautklima*
-       Für eine gut durchblutete und gesunde Kopfhaut mit glänzenden und
geschmeidigen Haaren*
-       Entfernt Schuppen und abgestorbene Hautpartikel
-       Verbessert natürlich die allgemeine Haarstruktur
-       Entwirrt langes und gelocktes Haar
-       Reinigt die Kopfhaut ohne Chemie*
-       Mehr Volumen im Haar
-       Mehr Stand im Haar durch Kräftigung der Haarbalkmuskulatur
-       Spart Shampoo und hilft Shampoo seltener und weniger zu nutzen
-       Nährstoffversorgung bis in die Haarspitzen
Inhaltsstoffe:
Care
Aloe Vera Direktsaft*, Decyl Glucoside, Coco Glucoside, Lauryl Glucoside, Hopfenextrakt*, Pentylene Glycol green, Meli..

```html
<!DOCTYPE html>
<html lang="de">
<head>
<meta charset="utf-8">
<title>Sol Verde – Shampoo Etiketten</title>
<link rel="stylesheet" href="https://fonts.googleapis.com/css2?family=Didact+Gothic&display=swap">
<style>
  :root {
    --page-bg: #f3f3f3;
    --label-bg: #ffffff;
    --sage: #b8d9aa;
    --apricot: #fad7a0;
    --ink: #111111;
    --brand-navy: #2b3486;
  }
  * { margin: 0; padding: 0; box-sizing: border-box; }
  html, body {
    width: 1200px; height: 1200px; overflow: hidden;
    background: var(--page-bg);
    font-family: "Didact Gothic", sans-serif;
    color: var(--ink);
  }
  .canvas { position: relative; width: 1200px; height: 1200px; }
  .label {
    position: absolute; top: 81px;
    width: 458px; height: 1039px;
    background: var(--label-bg);
    box-shadow: 0 6px 18px rgba(0,0,0,0.22);
    overflow: hidden;
  }
  .label--sensitiv { left: 112px; }
  .label--change { left: 630px; }
  .label svg.shapes { position: absolute; inset: 0; width: 100%; height: 100%; }
  .brand-name {
    position: absolute; left: 0; right: 0; text-align: center;
    font-size: 26px; line-height: 1; color: var(--brand-navy);
  }
  .product-name, .product-need, .product-type, .volume {
    position: absolute; left: 0; right: 0; text-align: center; line-height: 1;
  }
  .product-name { font-size: 70px; font-weight: 400; letter-spacing: 1px; }
  .product-need { font-size: 23px; letter-spacing: 0.5px; }
  .product-type { font-size: 15px; font-style: italic; }
  .volume { font-size: 15px; }
  .illustration { position: absolute; }
</style>
</head>
<body>
<main class="canvas">

  <section class="label label--sensitiv">
    <svg class="shapes" viewBox="0 0 458 1039" aria-hidden="true">
      <polygon points="59,0 227,0 239,57 79,94" fill="var(--sage)"/>
      <path d="M346,312 C360,300 378,306 388,314 C394,322 388,334 392,346 C400,368 408,380 398,394 C392,400 386,400 384,398 C378,384 372,372 362,362 C350,352 332,348 332,334 C332,324 338,318 346,312 Z" fill="var(--sage)"/>
    </svg>
    <p class="brand-name" style="top:128px;">Sol Verde</p>
    <h1 class="product-name" style="top:348px;">Sensitiv</h1>
    <p class="product-need" style="top:425px;">Empfindliche Kopfhaut</p>
    <p class="product-type" style="top:466px;">Shampoo</p>
    <div class="illustration" role="img" aria-label="Linienzeichnung einer Frau mit Ohrring, Blattzweigen und pastellfarbenen Flächen"
         style="left:37px; top:565px; width:391px; height:474px; background:radial-gradient(circle at 35% 55%, var(--apricot) 0 30%, transparent 31%), radial-gradient(ellipse at 78% 72%, var(--sage) 0 24%, transparent 40%), linear-gradient(180deg, #fff 0%, #fbf3e6 100%);"></div>
    <p class="volume" style="top:984px;">250ml</p>
  </section>

  <section class="label label--change">
    <svg class="shapes" viewBox="0 0 458 1039" aria-hidden="true">
      <path d="M68,0 L301,0 C270,24 230,50 190,62 C160,72 140,78 120,78 C90,78 72,40 68,0 Z" fill="var(--sage)"/>
      <path d="M80,319 C100,310 118,310 130,306 C150,298 166,292 180,294 C196,296 204,308 196,318 C184,330 164,332 150,342 C132,356 110,370 88,376 C70,380 63,366 63,350 C63,334 68,324 80,319 Z" fill="var(--apricot)"/>
    </svg>
    <p class="brand-name" style="top:119px;">Sol Verde</p>
    <h1 class="product-name" style="top:335px;">Change</h1>
    <p class="product-need" style="top:416px;">Strapaziertes Haar</p>
    <p class="product-type" style="top:457px;">Shampoo</p>
    <div class="illustration" role="img" aria-label="Linienzeichnung eines Frauenprofils mit Blattzweigen und apricotfarbener Fläche"
         style="left:0; top:618px; width:458px; height:421px; background:linear-gradient(90deg, #eef6ea 0%, #f7faf4 40%, #fdeed6 62%, var(--apricot) 72%, var(--apricot) 100%);"></div>
    <p class="volume" style="top:975px;">250ml</p>
  </section>

</main>
</body>
</html>
```